Fin-Tech Firm Captivating Business Card Design

We need a logo design as well to compliment this business card.

We are a new startup based in Singapore called 'Brevora Technologies'.

We develop an array of financial solutions ranging from payment convenience to forex trading and remittance.

Our initial product is Pim - an application which allows user to pre-order food items which would be ready for pickup upon arrival.

We would like to see designs being in black and silver or whatever that looks appealing and exudes a fun and professional feel.

We're not picky as long as it doesn't look like common business cards will do.

I do have a current logo which i do not really like. It will be attached for reference sake

Info:

Brevora Technologies Pte. Ltd.
Company Registration no. 201678213K

FILE TO BE IN .AI and .PSD

Target Market(s)

-F&B (Online-Ordering)
-Finance(P2P Lending and Forex)

Industry/Entity Type

Finance

Contact Information for Business Card

Name
Position
Contact
Email
Address: 47 Merrow Street, Calder House, #14-03 Singapore 068215

Adrian Teo
Founder, Managing Director
+65 98471360
adrian.t@brevoratech.com

Kai Loh
Founder, Executive Director
+65 96603847
kai.l@brevoratech.com

Logo Text

Brevora Technologies

Font styles to use
Sans Serif

Requirements
Must have
• Something that has word play about link brev
• Minimalistic but also something that catches The Eye
• Gold/silver on white/black might be nice
• Animal logo ; horse, eagle, bull or bear
Nice to have
• Just make it look fun and cute
• Just a suggestion to make the Y of brevora stand out
Should not have
• Any landmarks of singapore
• Exclude Pte. Ltd.

```html
<!DOCTYPE html>
<html lang="en">
<head>
<meta charset="utf-8">
<title>Brevora Technologies — Business Card</title>
<link href="https://fonts.googleapis.com/css2?family=Open+Sans:wght@400;600;700&display=swap" rel="stylesheet">
<style>
  :root {
    --gold-light: #fcc000;
    --gold-deep: #d6a300;
    --gold-text: #dda400;
    --white: #ffffff;
    --ink: #1a1a1a;
    --grey: #6e6e6e;
    --silver: #a9a9a9;
    --backdrop: #e9e6e2;
  }
  * { margin: 0; padding: 0; box-sizing: border-box; }
  html, body { width: 1200px; height: 900px; overflow: hidden; }
  body {
    background: var(--backdrop);
    font-family: "Open Sans", Arial, sans-serif;
    position: relative;
  }
  .card {
    position: absolute;
    border-radius: 14px;
    overflow: hidden;
    box-shadow: 0 6px 18px rgba(0,0,0,0.12);
  }
  .card-front { left: 78px; top: 35px; width: 588px; height: 363px; background: var(--white); }
  .card-back {
    left: 390px; top: 507px; width: 566px; height: 349px;
    background: linear-gradient(180deg, var(--gold-light), var(--gold-deep));
  }
  .gold-band {
    position: absolute; left: 0; right: 0; top: 28px; height: 99px;
    background: linear-gradient(180deg, var(--gold-light), var(--gold-deep));
  }
  .white-band { position: absolute; left: 0; right: 0; top: 80px; height: 96px; background: var(--white); }
  .emblem { position: absolute; border-radius: 50%; }
  .card-front .emblem {
    left: 232px; top: 14px; width: 126px; height: 126px;
    background: var(--silver);
    border: 9px solid var(--white);
  }
  .card-back .emblem {
    left: 229px; top: 72px; width: 106px; height: 106px;
    background: var(--gold-light);
    border: 8px solid var(--white);
  }
  .wordmark {
    position: absolute; left: 0; right: 0; text-align: center;
    font-weight: 400; letter-spacing: 2px; line-height: 1;
  }
  .card-front .wordmark { top: 146px; font-size: 50px; color: var(--gold-text); }
  .card-back .wordmark { top: 196px; font-size: 50px; color: var(--white); }
  .tagline {
    position: absolute; left: 0; right: 0; text-align: center;
    font-size: 15px; line-height: 1; display: flex; justify-content: center; align-items: center; gap: 6px;
  }
  .tagline::before, .tagline::after { content: ""; width: 30px; height: 1px; background: currentColor; }
  .card-front .tagline { top: 200px; color: var(--grey); }
  .card-back .tagline { top: 251px; color: var(--white); }
  .holder { position: absolute; left: 30px; top: 229px; }
  .holder-name { font-size: 20px; font-weight: 700; color: var(--gold-text); line-height: 1.2; }
  .holder-role { font-size: 15.5px; color: var(--ink); margin-top: 2px; }
  .contact { position: absolute; right: 36px; top: 231px; text-align: right; font-size: 15.5px; color: var(--ink); }
  .contact-line { display: flex; justify-content: flex-end; align-items: center; gap: 4px; height: 25px; }
  .contact-line svg { width: 12px; height: 12px; fill: var(--gold-text); }
  .registration { position: absolute; right: 36px; top: 289px; font-size: 15.5px; }
  .registration-label { color: var(--gold-text); font-weight: 600; }
  .registration-number { color: var(--ink); font-weight: 600; }
  .address { position: absolute; right: 36px; top: 321px; font-size: 15.5px; color: var(--ink); }
</style>
</head>
<body>
  <section class="card card-front">
    <div class="gold-band"></div>
    <div class="emblem"></div>
    <div class="wordmark">BREVORA</div>
    <div class="tagline">Technologies</div>
    <div class="holder">
      <div class="holder-name">Adrian Teo</div>
      <div class="holder-role">Founder, Managing Director</div>
    </div>
    <div class="contact">
      <div class="contact-line">+65 98471360
        <svg viewBox="0 0 24 24" aria-hidden="true"><path d="M6.6 10.8a15 15 0 0 0 6.6 6.6l2.2-2.2c.3-.3.7-.4 1-.2 1.1.4 2.3.6 3.6.6.6 0 1 .4 1 1V20c0 .6-.4 1-1 1A17 17 0 0 1 3 4c0-.6.4-1 1-1h3.5c.6 0 1 .4 1 1 0 1.3.2 2.5.6 3.6.1.3 0 .7-.2 1z"/></svg>
      </div>
      <div class="contact-line">adrian.t@brevoratech.com
        <svg viewBox="0 0 24 24" aria-hidden="true"><path d="M2 5h20v14H2z M2 5l10 8 10-8" stroke="#fff" stroke-width="1.5"/></svg>
      </div>
    </div>
    <div class="registration"><span class="registration-label">Company Registration no.</span> <span class="registration-number">201678213K</span></div>
    <div class="address">47 Merrow Street, Calder House, #14-03 Singapore 068215</div>
  </section>

  <section class="card card-back">
    <div class="white-band"></div>
    <div class="emblem"></div>
    <div class="wordmark">BREVORA</div>
    <div class="tagline">Technologies</div>
  </section>
</body>
</html>
```